Modern & Fresh Vantacor Book Cover

Need a creative e-book cover for my book.

Title: Master Vantacor Fast
Subtitle: Learn How To Easily Choose & Enroll in the Perfect Coverage at the Perfect Time.

Target Market(s)

60-70 year olds in the United States

Font styles to use
Sans Serif

Colors
9bcb3c
33a6d7

Requirements
Must have
• Must look modern and fresh.
• Use our company colors www.Movaquill.com

```html
<!DOCTYPE html>
<html lang="en">
<head>
<meta charset="utf-8">
<title>Master Vantacor Fast – Book Cover</title>
<link rel="stylesheet" href="https://fonts.googleapis.com/css2?family=Anton&family=Montserrat:wght@300;700&family=Oswald:wght@500&display=swap">
<style>
  :root {
    --cover-white: #ffffff;
    --brand-blue: #2c7bbd;
    --brand-green: #7dac3b;
    --rule-blue: #6aa0d0;
    --body-grey: #444444;
  }
  html, body {
    margin: 0;
    padding: 0;
    overflow: hidden;
    background: var(--cover-white);
  }
  .book-cover {
    display: block;
    width: 800px;
    height: 1200px;
    background: var(--cover-white);
  }
  .title-kicker {
    font-family: "Montserrat", sans-serif;
    font-weight: 700;
    font-size: 100px;
    fill: var(--brand-blue);
  }
  .title-rule {
    stroke: var(--rule-blue);
    stroke-width: 4;
  }
  .title-main {
    font-family: "Anton", sans-serif;
    fill: var(--brand-green);
    font-size: 151px;
  }
  .title-big {
    font-family: "Anton", sans-serif;
    fill: var(--brand-blue);
    font-size: 308px;
  }
  .subtitle {
    font-family: "Montserrat", sans-serif;
    font-weight: 300;
    font-size: 23px;
    fill: var(--body-grey);
  }
  .emblem {
    fill: var(--brand-green);
  }
  .author-name {
    font-family: "Oswald", sans-serif;
    font-weight: 500;
    font-size: 52px;
    fill: var(--brand-blue);
  }
</style>
</head>
<body>
<svg class="book-cover" viewBox="0 0 800 1200" xmlns="http://www.w3.org/2000/svg" aria-label="Book cover: Master Vantacor Fast">
  <g class="title-block">
    <line class="title-rule" x1="94" y1="111" x2="172" y2="111"/>
    <line class="title-rule" x1="628" y1="111" x2="706" y2="111"/>
    <text class="title-kicker" x="190" y="146" textLength="420" lengthAdjust="spacingAndGlyphs">MASTER</text>
    <text class="title-main" x="81" y="307" textLength="636" lengthAdjust="spacingAndGlyphs">VANTACOR</text>
    <text class="title-big" x="81" y="594" textLength="637" lengthAdjust="spacingAndGlyphs">FAST</text>
  </g>
  <g class="subtitle-block">
    <text class="subtitle" x="84" y="640" textLength="592" lengthAdjust="spacingAndGlyphs">Learn How To Easily Choose &amp; Enroll in the Perfect</text>
    <text class="subtitle" x="400" y="671" text-anchor="middle">Coverage at the Perfect Time.</text>
  </g>
  <circle class="emblem" cx="400" cy="888" r="163" role="img" aria-label="Circular maze emblem with a medical cross at its centre"/>
  <text class="author-name" x="228" y="1156" textLength="348" lengthAdjust="spacing">AUTHOR NAME</text>
</svg>
</body>
</html>
```